Walk Beside The River

Business Card design

Target Market(s)

People who require support in the commnity

Industry/Entity Type

Mental Health Support

Contact Information for Business Card

Mental Health Support Rosalind Tavener walkbesidetheriver@mailcove.com.au 0481 637 092 PO Box 926 Wattlebrook QLD 4587

Colors
6B429C
8869AF
B7A5CE
E3DAEB
F3F0F8

Requirements
Must have
• Logo & details listed above
Should not have
• No red or orange

```html
<!DOCTYPE html>
<html lang="en">
<head>
<meta charset="utf-8">
<title>Walk Beside The River – Business Card</title>
<link href="https://fonts.googleapis.com/css2?family=Montserrat:wght@500;600&display=swap" rel="stylesheet">
<style>
  :root {
    --page-bg: #232227;
    --card-dark: #1e1d22;
    --sun-yellow: #f2e92f;
    --sun-gold: #e2a93a;
    --brand-purple: #6b429c;
    --purple-light: #8869af;
    --text-light: #f3f0f8;
  }
  * { margin: 0; padding: 0; box-sizing: border-box; }
  html, body { width: 1200px; height: 780px; overflow: hidden; }
  body {
    background: var(--page-bg);
    font-family: "Montserrat", Arial, sans-serif;
    display: flex;
    align-items: center;
    justify-content: center;
    gap: 40px;
  }
  .card {
    position: relative;
    width: 540px;
    height: 310px;
    border-radius: 22px;
    overflow: hidden;
  }
  .card-front { border: 2px solid var(--sun-yellow); }
  .front-pattern {
    position: absolute;
    inset: 0;
    background: linear-gradient(160deg, #f6ef8a 0%, var(--sun-yellow) 40%, #eed038 75%, var(--sun-gold) 100%);
  }
  .card-back {
    background: var(--card-dark);
    border: 3px solid var(--sun-yellow);
  }
  .back-bands {
    position: absolute;
    inset: 0;
    width: 100%;
    height: 100%;
  }
  .brand {
    position: absolute;
    left: 26px;
    top: 20px;
    display: flex;
    align-items: center;
    gap: 14px;
  }
  .brand-dot {
    width: 80px;
    height: 80px;
    border-radius: 50%;
    background: var(--brand-purple);
  }
  .brand-name {
    font-weight: 600;
    font-size: 17px;
    color: var(--text-light);
    letter-spacing: 0.04em;
  }
  .details {
    position: absolute;
    left: 30px;
    top: 116px;
    color: var(--text-light);
    font-weight: 500;
    font-size: 15px;
    line-height: 1.4;
  }
  .contact-list { list-style: none; margin-top: 6px; }
  .contact-list li { display: flex; align-items: center; gap: 8px; }
  .contact-list svg { width: 13px; height: 13px; flex: none; }
</style>
</head>
<body>

<section class="card card-front">
  <div class="front-pattern" role="img" aria-label="Repeating golden star pattern on a yellow background"></div>
</section>

<section class="card card-back">
  <svg class="back-bands" viewBox="0 0 540 310" preserveAspectRatio="none" aria-hidden="true">
    <path d="M0 292 L300 292 C330 292 340 266 372 266 L540 266 L540 278 L376 278 C346 278 338 304 300 304 L0 304 Z" fill="var(--sun-yellow)"/>
    <path d="M376 252 L540 252 L540 262 L372 262 C360 262 362 252 376 252 Z" fill="var(--brand-purple)"/>
  </svg>

  <div class="brand">
    <span class="brand-dot"></span>
    <span class="brand-name">Walk Beside The River</span>
  </div>

  <div class="details">
    <p class="service">Mental Health Support</p>
    <p class="person">Rosalind Tavener</p>
    <ul class="contact-list">
      <li>
        <svg viewBox="0 0 24 24"><path d="M6.6 10.8a15 15 0 0 0 6.6 6.6l2.2-2.2a1 1 0 0 1 1-.25 11 11 0 0 0 3.6.6 1 1 0 0 1 1 1V20a1 1 0 0 1-1 1A17 17 0 0 1 3 4a1 1 0 0 1 1-1h3.5a1 1 0 0 1 1 1c0 1.25.2 2.45.6 3.6a1 1 0 0 1-.25 1z" fill="var(--sun-yellow)"/></svg>
        0481 637 092
      </li>
      <li>
        <svg viewBox="0 0 24 24"><rect x="2" y="5" width="20" height="14" rx="2" fill="none" stroke="var(--sun-yellow)" stroke-width="2"/><path d="M3 6l9 7 9-7" fill="none" stroke="var(--sun-yellow)" stroke-width="2"/></svg>
        walkbesidetheriver@mailcove.com.au
      </li>
      <li>
        <svg viewBox="0 0 24 24"><path d="M12 2a7 7 0 0 0-7 7c0 5 7 13 7 13s7-8 7-13a7 7 0 0 0-7-7zm0 9.5A2.5 2.5 0 1 1 12 6.5a2.5 2.5 0 0 1 0 5z" fill="var(--sun-yellow)"/></svg>
        PO Box 926 Wattlebrook QLD 4587
      </li>
    </ul>
  </div>
</section>

</body>
</html>
```